Basic / Quick Business Card

Quick easy design project!

Need a one sided basic business card that matches font & style of brand and bottle label for our gourmet condiment, Brindle Harrow Sauce. Brindle Harrow Sauce is sold in specialty retail, gourmet groceries and appears on chef-driven restaurant menus, so the target market is a high end, gourmet, artisan-made food-loving customer.

Files Included:
Sauce Bottle Label
Brindle Harrow Sauce Round Logos

**About the logos - the logo may be used in a circle or alone vertically as on side of the bottle label**

Layout of Card:
May be vertical or horizontal based on designer ideas.

Logo usage (in circle vs. stand alone vertical logo) is up to designers descretion as well.

Reverse side of business card will be various high end / professional product photos / food shots using us.kelbo.com system. **Designer on this project will NOT design a reserve for the card.**

Paper that will be used for printing:
Kelbo Standard - it's a WHITE paper, but we use a cream background on Brindle Harrow Sauce branding, so please take this into account on design to stay brand consistent.

Elements & Copy for Card:
1. Logo in either script horizontal or vertical version
2. Copy: "Artisan Made - Small Batch"
3. Name - Wes Dorrance
4. Title - Creator
5. Phone - xxx.xxx.xxxx
6. xxxx@brindleharrow.com
7. URL: brindleharrowsauce.com
8. Social Media: @getbrindleharrow on Quillo / Pagora / Lumigrid

Please provide final files in Illustrator or InDesign format.

```html
<!DOCTYPE html>
<html lang="en">
<head>
<meta charset="utf-8">
<title>Brindle Harrow Sauce — Business Card</title>
<link rel="stylesheet" href="https://fonts.googleapis.com/css2?family=Courier+Prime:wght@400;700&display=swap">
<style>
  :root {
    --backdrop: #e7e5e2;
    --ink: #1b1817;
    --saffron: #efa11a;
    --cream: #eeeadb;
  }
  * { box-sizing: border-box; margin: 0; padding: 0; }
  html, body {
    width: 871px; height: 1200px; overflow: hidden;
    background: var(--backdrop);
    font-family: "Courier Prime", "Courier New", monospace;
    color: var(--ink);
  }
  .card {
    position: absolute; left: 144px; top: 89px;
    width: 582px; height: 1022px;
    background: var(--ink);
  }
  .card__rule {
    position: absolute; inset: 15px;
    border: 4px solid var(--saffron);
  }
  .card__panel {
    position: absolute; inset: 26px;
    background: var(--cream);
  }
  .card__dotted-frame {
    position: absolute; inset: 20px;
    border: 3px dotted var(--saffron);
  }
  .brand-seal {
    position: absolute; left: 120px; top: 113px;
    width: 344px; height: 344px;
    border: 9px solid var(--ink);
    border-radius: 50%;
    display: flex; align-items: center; justify-content: center;
  }
  .brand-seal__name {
    font-weight: 700; font-size: 40px; line-height: 1.15;
    text-align: center; color: var(--ink);
  }
  .block { position: absolute; left: 0; right: 0; text-align: center; }
  .person__name { top: 498px; font-size: 41px; font-weight: 700; letter-spacing: 0.5px; }
  .person__title { top: 554px; font-size: 31px; letter-spacing: 5px; }
  .divider {
    position: absolute; left: 48px; right: 48px;
    border-top: 3px dotted var(--saffron);
  }
  .divider--1 { top: 620px; }
  .divider--2 { top: 770px; }
  .divider--3 { top: 854px; }
  .contact { top: 642px; font-size: 21px; font-weight: 700; line-height: 35px; }
  .social {
    position: absolute; left: 48px; right: 48px; top: 788px;
    height: 46px;
    display: flex; align-items: center; justify-content: center; gap: 18px;
    font-size: 21px; font-weight: 700;
  }
  .social__networks { color: var(--saffron); font-size: 18px; }
  .social__bar { width: 3px; height: 40px; background: var(--saffron); }
  .tagline { top: 874px; font-size: 22px; letter-spacing: 0.5px; }
</style>
</head>
<body>
  <div class="card">
    <div class="card__rule"></div>
    <div class="card__panel">
      <div class="card__dotted-frame"></div>

      <div class="brand-seal">
        <p class="brand-seal__name">Brindle<br>Harrow<br>Sauce</p>
      </div>

      <p class="block person__name">Wes Dorrance</p>
      <p class="block person__title">CREATOR</p>

      <div class="divider divider--1"></div>
      <p class="block contact">
        123.456.7890<br>
        dorrance@brindleharrow.com<br>
        www.brindleharrowsauce.com
      </p>
      <div class="divider divider--2"></div>

      <div class="social">
        <span class="social__networks">Quillo · Lumigrid · Pagora</span>
        <span class="social__bar"></span>
        <span class="social__handle">@getbrindleharrow</span>
      </div>

      <div class="divider divider--3"></div>
      <p class="block tagline">ARTISAN MADE - SMALL BATCH</p>
    </div>
  </div>
</body>
</html>
```